Computer Training in the Education sector - Letterhead

We need a new letter head to be designed for the company. We provide computer training fro the Education Sector, both primary and private tertiary providers. The colours will need to tie in with the website www.crossingthestream.co.nz.
The company name is Crossing the Stream with the tag line of Computer Training for Educators.
The footer will need to have the following detail...
0508 PCS MENTOR
021 839 415
www.crossingthestream.co.nz / training@crossingthestream.co.nz
Updates

Thanks for the designs so far.

Some have watermarks in the background. Please don't worry about using watermarks as I will not be using a watermark in in a final design.
Regards,
Roger

Thank you for all the designs and the effort. There was some great concepts that came through.

Cheers
Roger

Industry/Entity Type

Computer

```html
<!DOCTYPE html>
<html lang="en">
<head>
<meta charset="utf-8">
<title>Crossing the Stream – Letterhead</title>
<link href="https://fonts.googleapis.com/css2?family=Questrial&family=Arimo:wght@400;700&display=swap" rel="stylesheet">
<style>
  :root {
    --backdrop: #e9e6e2;
    --band: #18191b;
    --paper: #ffffff;
    --ink-light: #f2f2f2;
    --divider: #8a8a8a;
    --brand: #f08a2c;
  }
  * { box-sizing: border-box; margin: 0; padding: 0; }
  html, body {
    width: 1034px; height: 1200px; overflow: hidden;
    background: var(--backdrop);
  }
  .letterhead {
    position: absolute; left: 54px; top: 0;
    width: 926px; height: 1200px;
    background: var(--paper);
    display: flex; flex-direction: column;
  }
  .masthead {
    position: relative; height: 193px; background: var(--band);
  }
  .brand {
    position: absolute; left: 42px; top: 58px;
    display: flex; align-items: center; gap: 12px;
    font-family: "Questrial", sans-serif;
    color: var(--brand);
    font-size: 30px; line-height: 1.1;
  }
  .brand-dot {
    width: 22px; height: 22px; border-radius: 50%;
    background: var(--brand); flex: none;
  }
  .contact-divider {
    position: absolute; left: 582px; top: 60px;
    width: 1px; height: 82px; background: var(--divider);
  }
  .contact-list {
    position: absolute; left: 608px; top: 58px;
    list-style: none;
    font-family: "Questrial", sans-serif;
    font-size: 16px; letter-spacing: 0.4px;
    color: var(--ink-light);
  }
  .contact-list li {
    display: flex; align-items: center; gap: 6px;
    height: 22px; margin-bottom: 8px;
  }
  .contact-list svg { width: 13px; height: 13px; flex: none; }
  .letter-body { flex: 1; }
  .footer {
    position: relative; height: 63px; background: var(--band);
    color: var(--ink-light);
  }
  .tagline {
    position: absolute; left: 68px; top: 22px;
    font-family: "Arimo", sans-serif; font-weight: 700;
    font-size: 16px; letter-spacing: 2.2px;
  }
  .freephone {
    position: absolute; left: 632px; top: 16px;
    display: flex; align-items: center; gap: 6px;
    font-family: "Arimo", sans-serif;
    font-size: 21px; letter-spacing: 1px;
  }
  .freephone svg { width: 20px; height: 20px; }
</style>
</head>
<body>
  <div class="letterhead">
    <header class="masthead">
      <div class="brand"><span class="brand-dot"></span><span class="brand-name">Crossing the Stream</span></div>
      <div class="contact-divider"></div>
      <ul class="contact-list">
        <li>
          <svg viewBox="0 0 16 16" fill="none" stroke="currentColor" stroke-width="1.3"><circle cx="8" cy="8" r="7"/><path d="M6 4.5c-1 1-1 3 .5 5s3 2.5 4 1.5l-1.2-1.4-1 .5c-.6-.4-1.3-1.3-1.5-2l.8-.7z" fill="currentColor" stroke="none"/></svg>
          <span>021 839 415</span>
        </li>
        <li>
          <svg viewBox="0 0 16 16" fill="currentColor"><path d="M1 6l7-4 7 4v8H1z"/><path d="M2.5 6.5L8 10l5.5-3.5" stroke="#18191b" stroke-width="1.2" fill="none"/></svg>
          <span>training@crossingthestream.co.nz</span>
        </li>
        <li>
          <svg viewBox="0 0 16 16" fill="none" stroke="currentColor" stroke-width="1.1"><circle cx="8" cy="8" r="6.5"/><ellipse cx="8" cy="8" rx="3" ry="6.5"/><path d="M1.5 8h13M2.5 5h11M2.5 11h11"/></svg>
          <span>www.crossingthestream.co.nz</span>
        </li>
      </ul>
    </header>
    <main class="letter-body"></main>
    <footer class="footer">
      <p class="tagline">Computer Training for Educators</p>
      <p class="freephone">
        <svg viewBox="0 0 16 16" fill="none" stroke="currentColor" stroke-width="1.2"><circle cx="8" cy="8" r="7"/><path d="M6 4.5c-1 1-1 3 .5 5s3 2.5 4 1.5l-1.2-1.4-1 .5c-.6-.4-1.3-1.3-1.5-2l.8-.7z" fill="currentColor" stroke="none"/></svg>
        <span>0508 PCS MENTOR</span>
      </p>
    </footer>
  </div>
</body>
</html>
```